Business Cards - Brightpath Horizon

need to design unique business card for my mortgage business. I need to design credit card style business card for my business or any unique idea that you might have

Target Market(s)

Home Loan customers

Industry/Entity Type

Mortgage Brokerage

Contact Information for Business Card

please design credit card style or very unique style business card

Colors

Designer to choose colors to be used in the design.

Requirements
Must have
• Name
• position
• Phone number
• fax number
• email address
• website address
• social media address
• All above fields will be provided once design in finalised

```html
<!DOCTYPE html>
<html lang="en">
<head>
<meta charset="utf-8">
<title>Brightpath Horizon – Business Cards</title>
<link rel="stylesheet" href="https://fonts.googleapis.com/css2?family=Roboto:wght@400;500;700&family=Roboto+Condensed:wght@500;700&family=Share+Tech+Mono&display=swap">
<style>
  :root{
    --bg:#3a3a3c;
    --paper:#fbfbfb;
    --navy:#1a2fb0;
    --navy-deep:#0a1560;
    --royal:#2a3fd6;
    --sky:#17a9e8;
    --orange:#f7941d;
    --gold:#f2d23c;
    --ink:#4a4a4a;
    --white:#ffffff;
  }
  *{box-sizing:border-box;margin:0;padding:0}
  html,body{width:1200px;height:886px;overflow:hidden}
  body{background:var(--bg);font-family:"Roboto",sans-serif;position:relative}
  .card{position:absolute;top:273px;width:540px;height:340px;border-radius:22px;background:var(--paper);overflow:hidden;box-shadow:0 12px 30px rgba(0,0,0,.45)}
  .card--front{left:40px}
  .card--back{left:620px}

  .tree-art{position:absolute;right:34px;top:22px;width:180px;height:190px;border-radius:48% 48% 20% 20%;background:radial-gradient(ellipse at 50% 38%,#2cbaf0 0%,var(--sky) 55%,#0f93d4 100%)}

  .brand{position:absolute;display:flex;align-items:center;gap:10px}
  .brand__dot{width:22px;height:22px;border-radius:50%;background:var(--orange);flex:none}
  .brand__name{font-family:"Roboto Condensed",sans-serif;font-weight:700;color:var(--navy);text-transform:uppercase;letter-spacing:.5px;line-height:1;white-space:nowrap}
  .card--front .brand{left:34px;bottom:74px}
  .card--front .brand__name{font-size:30px}
  .web-line{position:absolute;left:66px;bottom:46px;font-size:13px;letter-spacing:3px;color:var(--ink)}

  .card--back .brand{left:34px;top:92px}
  .card--back .brand__name{font-size:26px}

  .social{position:absolute;right:42px;top:30px;display:flex;gap:6px}
  .social span{width:24px;height:24px;border-radius:50%}
  .social .s1{background:#dd4b39}.social .s2{background:#3b5998}.social .s3{background:#1da1f2}.social .s4{background:#0e76a8}
  .person{position:absolute;right:42px;top:66px;text-align:right;font-family:"Roboto Condensed",sans-serif}
  .person__name{font-size:19px;font-weight:700;color:var(--navy);letter-spacing:.3px}
  .person__role{font-size:14px;font-weight:500;color:var(--orange);margin-top:2px}

  .band{position:absolute;left:0;right:0;top:150px;bottom:0;background:linear-gradient(160deg,var(--royal) 0%,#1628a8 45%,var(--navy-deep) 100%)}
  .card-number{position:absolute;right:40px;top:24px;font-family:"Share Tech Mono",monospace;font-size:30px;letter-spacing:3px;color:var(--gold);word-spacing:8px;white-space:nowrap}
  .contact{position:absolute;left:34px;bottom:26px;color:var(--white);font-size:13px;line-height:1.45}
  .contact b{font-weight:700}
  .contact__rule{width:60px;height:2px;background:var(--white);margin:8px 0 7px}
</style>
</head>
<body>
  <section class="card card--front" aria-label="Card front">
    <div class="tree-art" role="img" aria-label="Illustration of a large leafy tree in sky blue"></div>
    <div class="brand"><span class="brand__dot"></span><span class="brand__name">Brightpath Horizon</span></div>
    <p class="web-line">www.brightpathhorizon.com</p>
  </section>

  <section class="card card--back" aria-label="Card back">
    <div class="brand"><span class="brand__dot"></span><span class="brand__name">Brightpath Horizon</span></div>
    <div class="social" aria-label="Social media"><span class="s1"></span><span class="s2"></span><span class="s3"></span><span class="s4"></span></div>
    <div class="person">
      <p class="person__name">MAYA ELLISON</p>
      <p class="person__role">CEO/FOUNDER</p>
    </div>
    <div class="band">
      <p class="card-number">512 806 3749</p>
      <div class="contact">
        <p><b>F:</b> 415 730 2291</p>
        <p><b>E:</b> hello@brightpathhorizon.com</p>
        <p><b>W:</b> www.brightpathhorizon.com</p>
        <div class="contact__rule"></div>
        <p>1240 Cedar Ridge Road</p>
        <p>Juneau, Alaska 99801</p>
      </div>
    </div>
  </section>
</body>
</html>
```